VELTAR WEBSITE

need to create a new website for VELTAR ltd
the company deals with all aspects of safety products & safety wear
we need a simple website to show
ideas can be taken from following website whose products we shall distribute in kenya
www.kwr.co.uk
www.dorvik.eu
www.brimtoolsupplyco.com
www.gardvalewerks.co.za

we need following tabs
1) home - basic company information
2) products - broken down to following categories ie gloves, head protection, ear protection, mouth protection, foot protection
3) contacts

the company profile is a reputable company dealing with all aspects of safety, HSE (health and safety equipment), and PPE (personal protective equipment)

the website should have the dorvik logo for which we are an authorized distributor.
the dorvi industrial range writeup can be picked from their website
Updates

Dear Designers, i shall be able to choose a final design in 2 weeks, sorry i have not been able to finalise this due to a personal reason

Target Market(s)

the buyers are all types of industry who care for their employees safety

Industry/Entity Type

Industrial

Requirements
Must have
• clean look, fresh look, user freindly
Nice to have
• clear images, quick links etc

```html
<!DOCTYPE html>
<html lang="en">
<head>
<meta charset="utf-8">
<title>VELTAR – Specialized Protective &amp; Industrial Products</title>
<link href="https://fonts.googleapis.com/css2?family=Open+Sans:wght@300;400;600;700&family=Roboto+Condensed:wght@400;700&family=Roboto:wght@400;700&display=swap" rel="stylesheet">
<style>
:root{
  --yellow:#f5b800;
  --ink:#2b2e33;
  --text:#555a60;
  --muted:#8a8f94;
  --line:#e6e6e6;
  --footer:#303337;
  --footer-deep:#25282b;
  --footer-text:#c9ccd0;
  --white:#ffffff;
}
*{margin:0;padding:0;box-sizing:border-box}
html,body{width:853px;height:1200px;overflow:hidden;background:var(--white)}
body{position:relative;font-family:'Open Sans',sans-serif;color:var(--text)}
.abs{position:absolute}
.top-strip{left:0;top:0;width:853px;height:3px;background:var(--yellow)}

/* header */
.brand{left:78px;top:40px;display:flex;align-items:center;gap:8px}
.brand-mark{width:22px;height:22px;background:var(--yellow)}
.brand-name{font-family:'Open Sans',sans-serif;font-weight:700;font-size:32px;color:var(--ink);letter-spacing:1px}
.social{left:680px;top:17px;display:flex;gap:5px}
.social span{width:14px;height:14px;border-radius:50%}
.call{left:644px;top:42px;display:flex;align-items:center;gap:6px}
.call-text{font-size:12px;line-height:14px;color:var(--ink)}
.call-text b{font-weight:400;font-size:13.5px}
.nav{top:80px;font-size:11.5px;color:var(--text);line-height:20px}
.nav.active{background:var(--yellow);color:var(--white);padding:0 6px}
.header-rule{left:0;top:122px;width:853px;height:1px;background:#eeeeee}

/* intro */
.intro-title{left:0;width:853px;top:142px;text-align:center;font-weight:300;font-size:24px;color:var(--text)}
.intro-title em,.band-title em,.slide-kicker{font-style:normal;color:var(--yellow);font-weight:600}
.intro-text{left:126px;width:600px;top:178px;text-align:center;font-weight:300;font-size:13px;line-height:16.5px;color:var(--muted)}

/* hero */
.hero{left:0;top:249px;width:853px;height:319px;background:linear-gradient(180deg,#b9cde0 0%,#d8dde0 40%,#b79a74 75%,#9c7d59 100%)}
.hero-band{left:0;top:526px;width:853px;height:42px;background:rgba(240,240,240,.92)}
.band-title{left:81px;top:533px;font-weight:300;font-size:19px;color:var(--ink)}
.dots{left:731px;top:546px;display:flex;gap:1.5px}
.dots span{width:7px;height:7px;border-radius:50%;background:#bdbdbd}
.dots span:first-child{background:var(--ink)}
.slide-card{left:114px;top:305px;width:237px;height:165px;background:rgba(255,255,255,.95);border-top:4px solid var(--yellow);padding:10px 12px}
.slide-kicker{font-size:19px;line-height:22px;display:block}
.slide-title{font-weight:300;font-size:22px;line-height:24px;color:var(--ink)}
.slide-text{font-size:10.5px;line-height:14.5px;color:var(--muted);margin-top:6px;font-weight:300}
.slide-link{display:block;margin-top:6px;font-size:11px;color:var(--yellow);text-decoration:underline}

/* services */
.service{top:588px;width:160px;text-align:center}
.service svg{display:block;margin:0 auto}
.service h3{font-weight:400;font-size:15px;color:var(--ink);margin-top:4px}
.service p{font-size:9px;line-height:13px;color:var(--muted);margin-top:3px}
.view-all{left:690px;width:85px;top:719px;text-align:right;font-size:10.5px;color:var(--ink);text-decoration:underline}

/* feature + news */
.sec-head{top:742px;display:flex;align-items:center;gap:10px}
.sec-kicker{font-family:'Roboto Condensed',sans-serif;font-size:7.5px;color:var(--muted);line-height:8px}
.sec-title{font-family:'Roboto Condensed',sans-serif;font-size:14px;color:var(--ink);line-height:16px}
.all-news{left:702px;top:757px;font-family:'Roboto Condensed',sans-serif;font-size:7.5px;color:#b0b0b0;border-left:1px solid var(--line);padding-left:10px}
.rule{top:778px;height:1px;background:var(--line)}
.tabs{left:78px;top:793px;width:175px;border-right:1px solid var(--line)}
.tab{height:32px;line-height:32px;text-align:right;padding-right:14px;font-family:'Roboto',sans-serif;font-size:8.5px;letter-spacing:.5px;color:var(--muted);border-bottom:1px solid var(--line)}
.tab.active{border:1px solid var(--line);border-left:2px solid var(--yellow);border-right:none;background:var(--white)}
.feature-body{left:268px;top:793px;width:230px;font-family:'Roboto',sans-serif}
.feature-body h4{font-size:8.5px;font-weight:700;color:var(--ink);margin-bottom:8px}
.feature-body p{font-size:8.3px;line-height:13.6px;color:var(--muted);margin-bottom:11px}
.news-photo{left:514px;top:793px;width:261px;height:85px;background:linear-gradient(180deg,#5a4a5a 0%,#c98a72 45%,#7a7f8a 70%,#3c3c44 100%)}
.news-date{left:524px;top:894px;width:46px;height:46px;background:var(--white);box-shadow:0 1px 3px rgba(0,0,0,.2);text-align:center;font-family:'Roboto Condensed',sans-serif;font-size:32px;line-height:46px;color:var(--ink)}
.news-month{left:524px;width:46px;top:946px;text-align:center;font-family:'Roboto Condensed',sans-serif;font-size:7.5px;color:var(--muted)}
.news-meta{left:584px;top:894px;font-family:'Roboto Condensed',sans-serif;font-size:6.8px;color:#a8a8a8}
.news-title{left:584px;top:905px;font-family:'Roboto Condensed',sans-serif;font-size:12px;color:var(--ink)}
.news-text{left:584px;top:928px;width:190px;font-family:'Roboto',sans-serif;font-size:8.3px;line-height:13.5px;color:var(--muted)}

/* footer */
.footer{left:0;top:995px;width:853px;height:170px;background:var(--footer)}
.footer-bottom{left:0;top:1165px;width:853px;height:35px;background:var(--footer-deep)}
.f-col{top:1008px}
.f-col h5{font-size:10px;font-weight:400;color:var(--white);margin-bottom:3px;letter-spacing:.2px}
.f-col li{list-style:none;font-size:8.5px;line-height:14.4px;color:var(--footer-text)}
.f-input{left:560px;top:1030px;width:197px;height:23px;background:#3d4045;border:1px solid #4a4d52;font-size:8px;color:#9ea2a6;padding:6px 8px}
.f-btn{left:704px;top:1064px;width:53px;height:17px;background:var(--yellow);color:var(--ink);font-size:9px;text-align:center;line-height:17px}
.f-tweet-h{left:558px;top:1083px;font-size:10px;color:var(--white)}
.f-tweet{left:560px;top:1103px;width:200px;font-size:8px;line-height:14px;color:var(--footer-text)}
.copy{left:90px;top:1176px;font-size:8.5px;color:var(--footer-text)}
.legal{left:634px;top:1176px;font-size:8.5px;color:var(--footer-text)}
</style>
</head>
<body>
<div class="abs top-strip"></div>

<header>
  <div class="abs brand"><span class="brand-mark"></span><span class="brand-name">VELTAR</span></div>
  <div class="abs social" aria-label="Social links">
    <span style="background:#ea4c89"></span><span style="background:#cb2027"></span><span style="background:#3b5998"></span><span style="background:#1da1f2"></span><span style="background:#3f729b"></span>
  </div>
  <div class="abs call">
    <svg width="22" height="28" viewBox="0 0 22 28" aria-hidden="true"><path d="M3 14a8 8 0 0 1 16 0" fill="none" stroke="#2b2e33" stroke-width="2"/><rect x="1" y="13" width="5" height="9" rx="2" fill="#2b2e33"/><rect x="16" y="13" width="5" height="9" rx="2" fill="#2b2e33"/><path d="M18 22q0 4-6 4" fill="none" stroke="#2b2e33" stroke-width="1.4"/></svg>
    <div class="call-text">Call Now<br><b>0800-5550-123-4</b></div>
  </div>
  <nav>
    <span class="abs nav active" style="left:419px">Home</span>
    <span class="abs nav" style="left:482px">About Us</span>
    <span class="abs nav" style="left:556px">Our Products</span>
    <span class="abs nav" style="left:650px">Agencies</span>
    <span class="abs nav" style="left:722px">Contact Us</span>
  </nav>
  <div class="abs header-rule"></div>
</header>

<section>
  <h1 class="abs intro-title"><em>VELTAR</em> Specialized Protective &amp; Industrial Products</h1>
  <p class="abs intro-text">Lorem ipsum dolor sit amet, consectetur adipisicing elit, sed do eiusmod tempor incididunt ut labore et dolore magna aliqua. Ut enim ad minim veniam, quis nostrud exercitation ullamco laboris nisi ut aliquip ex ea commodo consequat.</p>
</section>

<section>
  <div class="abs hero" role="img" aria-label="Smiling oil field worker in a yellow hard hat and orange hi-vis jacket in front of pump jacks under a cloudy sky"></div>
  <div class="abs slide-card">
    <span class="slide-kicker">VELTAR</span>
    <div class="slide-title">Head Protection</div>
    <p class="slide-text">Lorem ipsum dolor sit amet, consectetur adipisicing elit, sed do eiusmod tempor incididunt ut labore et dolore magna aliqua...</p>
    <span class="slide-link">READ MORE</span>
  </div>
  <div class="abs hero-band"></div>
  <h2 class="abs band-title"><em>VELTAR</em> Specialized Protective <em>&amp;</em> Industrial Products</h2>
  <div class="abs dots"><span></span><span></span><span></span><span></span><span></span></div>
</section>

<section>
  <div class="abs service" style="left:73px">
    <svg width="44" height="44" viewBox="0 0 44 44" aria-hidden="true"><circle cx="22" cy="22" r="22" fill="#2b2e33"/><path d="M14 30 28 16M16 14l14 16" stroke="#fff" stroke-width="3.5" stroke-linecap="round"/></svg>
    <h3>Tool Division</h3><p>Lorem ipsum dolor sit amet consec-<br>tetur adipsicing elit, Sed euismod<br>tempor incidunt...</p>
  </div>
  <div class="abs service" style="left:255px">
    <svg width="44" height="44" viewBox="0 0 44 44" aria-hidden="true"><circle cx="22" cy="22" r="22" fill="#2b2e33"/><path d="M11 27a11 11 0 0 1 22 0z" fill="#fff"/><rect x="9" y="27" width="26" height="3" rx="1.5" fill="#fff"/></svg>
    <h3>Safety Division</h3><p>Lorem ipsum dolor sit amet consec-<br>tetur adipsicing elit, Sed euismod<br>tempor incidunt...</p>
  </div>
  <div class="abs service" style="left:438px">
    <svg width="44" height="44" viewBox="0 0 44 44" aria-hidden="true"><circle cx="22" cy="22" r="22" fill="#2b2e33"/><path d="M13 22l6 6 12-12" fill="none" stroke="#fff" stroke-width="4" stroke-linecap="round" stroke-linejoin="round"/></svg>
    <h3>Veltar</h3><p>Lorem ipsum dolor sit amet consec-<br>tetur adipsicing elit, Sed euismod<br>tempor incidunt...</p>
  </div>
  <div class="abs service" style="left:621px">
    <svg width="44" height="44" viewBox="0 0 44 44" aria-hidden="true"><circle cx="22" cy="22" r="22" fill="#2b2e33"/><circle cx="22" cy="22" r="15" fill="none" stroke="#fff" stroke-width="2"/><path d="M16 15q-2 4 2 9t9 5l2-3-3-2-2 1q-3-2-4-5l1-2-2-3z" fill="#fff"/></svg>
    <h3>Contact Us</h3><p>Lorem ipsum dolor sit amet consec-<br>tetur adipsicing elit, Sed euismod<br>tempor incidunt...</p>
  </div>
  <span class="abs view-all">View All Services</span>
</section>

<section>
  <div class="abs sec-head" style="left:78px">
    <svg width="24" height="20" viewBox="0 0 24 20" aria-hidden="true"><circle cx="8" cy="12" r="6" fill="none" stroke="#888" stroke-width="3" stroke-dasharray="2.5 1.5"/><circle cx="18" cy="5" r="3.5" fill="none" stroke="#888" stroke-width="2" stroke-dasharray="2 1.2"/></svg>
    <div><div class="sec-kicker">JUST DO IT!!</div><div class="sec-title">OUR MAIN FEATURE</div></div>
  </div>
  <div class="abs sec-head" style="left:513px">
    <svg width="24" height="22" viewBox="0 0 24 22" aria-hidden="true"><path d="M2 14 14 2l8 8-12 12z" fill="none" stroke="#999" stroke-width="1.6"/><path d="M7 14l7-7M10 16l6-6" stroke="#999" stroke-width="1.2"/></svg>
    <div><div class="sec-kicker">Small subtitle here</div><div class="sec-title">NEWS FROM CATEGORY</div></div>
  </div>
  <span class="abs all-news">All news</span>
  <div class="abs rule" style="left:78px;width:424px"></div>
  <div class="abs rule" style="left:513px;width:262px"></div>

  <div class="abs tabs">
    <div class="tab active">HEAD PROTECTION</div>
    <div class="tab">HAND PROTECTION</div>
    <div class="tab">MOUTH PROTECTION</div>
    <div class="tab">FOOT PROTECTION</div>
  </div>
  <div class="abs feature-body">
    <h4>LOREM IPSUM DOLOR SIT AMET</h4>
    <p>Lorem ipsum dolor sit amet, movet contentiones vis et, ex nec erat placerat. Nam feugiat hendrerit interpretaris ut, in nam...</p>
    <p>Lorem ipsum dolor sit amet, movet contentiones vis et, ex nec erat placerat. Sed do euismod tempor incidunt magna aliqua Nam feugiat hendrerit interpretaris ut lorem ipsum dolor sit amet, movet contentiones vis et, ex nec erat placerat. Sed do euismod tempor incidunt magna aliqua Nam feugiat hendrerit interpretaris ut, in nam...</p>
  </div>

  <div class="abs news-photo" role="img" aria-label="Waterfall over icy rocks at sunset under a pink sky"></div>
  <div class="abs news-date">02</div>
  <div class="abs news-month">MAR.</div>
  <div class="abs news-meta">FERROW TEAM POST, WATER, WATERFALL LEAVE A COMMENT</div>
  <div class="abs news-title">Amazing waterfall</div>
  <p class="abs news-text">Lorem ipsum dolor sit amet, movet contentiones vis et, ex nec erat placerat. Nam feugiat hendrerit interpretaris ut, in nam...</p>
</section>

<footer>
  <div class="abs footer"></div>
  <div class="abs f-col" style="left:89px"><h5>QUICK LINKS</h5><ul><li>Home</li><li>About Us</li><li>Our Products</li><li>Agencies</li><li>Contact Us</li></ul></div>
  <div class="abs f-col" style="left:244px"><h5>OUR SERVICES</h5><ul><li>Lorem</li><li>Ipsum Dolor</li><li>Sit Amet</li><li>Consectetur</li><li>Adipsicing Elit</li><li>Perspiciatis</li><li>Totam Rem</li></ul></div>
  <div class="abs f-col" style="left:404px"><h5>ABOUT VELTAR</h5><ul><li>Lorem</li><li>Ipsum Dolor</li><li>Sit Amet</li><li>Consectetur</li><li>Adipsicing Elit</li></ul></div>
  <div class="abs f-col" style="left:558px"><h5>SUBSCRIBE TO OUR E-NEWSLETTER</h5></div>
  <div class="abs f-input">Enter your email address...</div>
  <div class="abs f-btn">Subscribe</div>
  <div class="abs f-tweet-h">LATEST TWEET</div>
  <p class="abs f-tweet">The #Friendliest and Unfriendliest #Cities in the World http://www.dailydolor.net/daily-dolor /2013/07/world-Veltar-dublin-auck-cork-friendly-u</p>
  <div class="abs footer-bottom"></div>
  <div class="abs copy">© Copyrights 2013 All rights Reserved</div>
  <div class="abs legal">Privacy Policy &nbsp;&nbsp;|&nbsp;&nbsp; Terms Of Uses</div>
</footer>
</body>
</html>
```